EXCITING DECK for Automotive dealers that shows how our Technology works.

General Concept
The deck should visually represent the Trade and Credit Lead Life Cycle program is a dynamic, interconnected journey, illustrating how leads are generated, nurtured, and converted. The focus should be on how your system flows seamlessly between credit and trade-in opportunities for consumers, with the goal of maximizing engagement and conversions.
Slide 1: Title Slide - Lead Life Cycle Program
• Visual Concept: A stylized cycle or wheel that represents the stages of the lead life cycle, with arrows connecting each stage.
• Headline: "Lead Life Cycle Program"
• Subhead line: "Credit Pre-Qualification and Trade-In Appraisal"
• Imagery: Modern, sleek graphics of vehicles, smartphones (for texting), email icons, and dollar signs for value.
Slide 2: Lead Generation Sources
• Visual Concept: A funnel with the top representing the different lead generation sources.
• Content:
o Top of Funnel (Leads Enter):
 Pre-Qualification Tool (Fast4Loan)- How it Works
 1. Converts Web Traffic into the highest quality lead on the market
 Vorqel Email/Mail Marketing – How it Works
 1. Delivers actionable leads from email marketing not Just OPENS AND CLICKS. Show the text demo. Audiences below
1. Past Sold Customers (Equity Targets)
2. Past Service Onlu Department Customers (Conquest Sales)
3. Unsold Leads (from previous interactions)
o Each source should have a distinct icon to represent it (e.g., envelope for email, a wrench for past service customers, etc.).
• Headline: "Multiple Lead Sources Feeding into the Program"
• Imagery: The funnel narrowing toward the next step with leads symbolized by icons flowing downward.
Slide 3: Credit Leads - Pre-Qualified Flow
• Visual Concept: A customer engaging with the Fast4Loan tool on their mobile, being pre-qualified, and then us sending a offer to appraise their trade.
• Flow Explanation:
o Customer pre-qualifies via Fast4Loan → Receives credit approval → Email and Mail Example to check trade-in value.
• Headline: "Pre-Qualified Leads: Offering Trade-In Appraisal"
• Imagery: A sequence that shows how a customer moves from pre-qualification to considering their trade-in value. To purchasing
Slide 4: Trade-In Leads - Valuation Flow
• Visual Concept: A customer who has received a trade-in valuation offer now being prompted to pre-qualify for financing.
• Flow Explanation:
o Customer texts for vehicle value → Receives trade-in appraisal → Offer to pre-qualify for financing appears link is at the bottom of the text response.
• Headline: "Trade-In Leads: Offering Credit Pre-Qualification"
• Imagery: A customer looking at their trade-in value on their phone and being shown an additional prompt to pre-qualify for a loan.
Slide 5: Cross-Offer Opportunities
• Visual Concept: A two-way street or cycle, illustrating the seamless transition between offering pre-qualification to trade-in customers and offering trade-in value to credit leads.
• Content:
o Two pathways:
1. Start as a Credit Lead → Offer Trade-In Valuation
2. Start as a Trade-In Lead → Offer Credit Pre-Qualification
o Headline: "Cross-Offer Opportunities for Maximum Engagement"
• Imagery: Arrows going in both directions, symbolizing the back-and-forth opportunities between credit and trade leads.
Digital Retargeting for Cross-Action Engagement
• Visual Concept: An omnichannel approach with a customer in the center, surrounded by email/Mail icons, Chatterbook, and Snapgrove logos. Arrows leading from each platform back to the customer, showing how these channels drive engagement.
• Content:
o Title: "Engage to Convert one lead type to get both with Email/Mail and Digital Retargeting"
o Explanation:
 Whether a lead starts as a Pre-Qualified Credit Lead or a Trade-In Valuation Lead, we use personalized Email/Mail Campaigns and Digital Retargeting Ads (Chatterbook & Snapgrove) to encourage them to take the next action.
 If they pre-qualify for credit, we retarget them with trade-in valuation offers.
 If they start with a trade-in valuation, we follow up with financing offers.
o Headline: "Leverage Email & Social Retargeting to Drive Cross-Action"
• Visuals:
o Icons of Email, Chatterbook, and Snapgrove: Showing the platforms through which you retarget leads.
o Customer Journey Map: Illustrating how leads who interacted once are guided to the next step (credit lead → trade-in offer, trade-in lead → pre-qualification).
o Arrows Flowing Between Channels: Showing how no matter where a lead starts, they are continually engaged through digital touchpoints until they complete both actions.
o Ad examples
• Call to Action: "Stay Top of Mind and Convert Leads into Multi-Action Customers"
This slide emphasizes how you’re leveraging both email/mail marketing and social media retargeting to move leads further along the customer journey, regardless of how they entered your funnel. The visuals should reinforce the idea of continuous engagement and omnipresent reminders for them to take action.
________________________________________
Slide 6: Lifecycle Representation
• Visual Concept: A circular diagram showing how leads can continuously move between credit and trade offers throughout their lifecycle.
• Content:
o Show how the lifecycle doesn’t end after one interaction, but can continue with follow-up offers.
o Headline: "Continuous Engagement Throughout the Lead Life Cycle"
• Imagery: Circular arrows or flowchart representing each stage looping back into the lifecycle, emphasizing that leads can be re-engaged.
Slide 7: Lead Conversion Goals
• Visual Concept: A progression from leads to successful transactions (e.g., a customer with keys to a new car). Showing that getting customers to take both of these actions delives a lead that is very committed to the process of buying.
• Content:
o End goal: Convert both credit and trade leads into sales.
o Show statistics or success metrics as optional data points.
o Headline: "Converting Leads into Sales"
• Imagery: A car dealership handing over keys, happy customers, and sold vehicles.
Slide 8: Next Steps / Call to Action
• Visual Concept: A final slide summarizing the key takeaways and next steps.
• Headline: "Maximize Lead Potential with Cross-Offer Opportunities"
• Imagery: A mix of credit leads, trade leads, and successful customer outcomes.
________________________________________These slides should be clean and modern, using simple but impactful visuals like arrows, icons, and flow diagrams to represent the journey. The key is to emphasize flow and interaction between credit and trade-in opportunities, showing the two-way cross-sell nature of your Lead Life Cycle Program.

I have attached a current deck so you can pull some basic product info and graphics into the new deck (PLEASE DONT JUST COPY THE OLD DECK). I have also included some of our email artwrok if you need it. If you want to look at our website go here www.plorvenadsgroup.example

Target Market(s)

Car Dealers

Industry/Entity Type

Automotive Marketing

Requirements
Must have
• PLEASE READ THE PROJECT DESCRIPTION
Nice to have
Should not have
• PLEASE dont just copy the deck i uploaded. I am looking for a differnt take.

```html
<!DOCTYPE html>
<html lang="en">
<head>
<meta charset="utf-8">
<title>Lead Life Cycle Program Deck</title>
<link href="https://fonts.googleapis.com/css2?family=Montserrat:wght@400;500;600&display=swap" rel="stylesheet">
<style>
:root{
  --board:#bdbdbd;
  --paper:#ffffff;
  --red:#e10a1e;
  --ink:#2b2b2f;
  --slate:#3d3d42;
  --muted:#5a5a60;
  --soft:#ececec;
}
*{box-sizing:border-box;margin:0;padding:0}
html,body{width:1200px;height:410px;overflow:hidden;background:var(--board)}
body{position:relative;font-family:'Montserrat',sans-serif;color:var(--ink)}
.slide{position:absolute;width:245px;height:137px;background:var(--paper);overflow:hidden}
.rule{position:absolute;left:12px;top:10px;width:52px;height:1px;background:linear-gradient(90deg,var(--red) 50%,var(--slate) 50%)}
.brand{position:absolute;right:6px;top:7px;display:flex;align-items:center;gap:3px;font-size:6px;font-weight:600;color:var(--ink);letter-spacing:.3px}
.brand i{display:block;width:6px;height:6px;background:var(--red)}
.title{position:absolute;left:12px;top:17px;width:160px;font-size:8px;line-height:9.6px;font-weight:500;color:var(--red)}
.subtitle{position:absolute;left:12px;top:31px;font-size:4.6px;color:var(--ink)}
.footer{position:absolute;left:0;bottom:0;width:100%;height:10px;display:flex;font-size:3.6px;color:#fff}
.footer .copy{flex:0 0 79%;background:var(--red);padding-left:13px;line-height:10px}
.footer .page{flex:1;background:var(--slate);margin-left:1px;text-align:center;line-height:10px}
.label{position:absolute;font-size:3.8px;text-align:center;color:var(--ink);line-height:5px}
.small{position:absolute;font-size:3.2px;line-height:4.3px;color:var(--muted)}
.photo{position:absolute}
.bubble{position:absolute;background:#fff;border-radius:50%;font-size:3.4px;color:var(--red);text-align:center;display:flex;align-items:center;justify-content:center;line-height:4px;box-shadow:0 0 2px rgba(0,0,0,.2)}
svg{position:absolute;left:0;top:0;overflow:visible}
</style>
</head>
<body>

<!-- Slide 1 -->
<section class="slide" style="left:51px;top:51px">
  <div class="rule"></div>
  <div class="brand"><i></i>Plorven Ads</div>
  <h1 class="title" style="top:18px">Lead Life Cycle Program</h1>
  <p class="subtitle">Credit Pre-Qualification and Trade-In Appraisal</p>
  <svg width="245" height="137">
    <g fill="none" stroke="var(--ink)">
      <circle cx="31" cy="74" r="17" stroke-width="1.3"/><circle cx="31" cy="74" r="14" stroke-width=".3" stroke-dasharray="1 .6"/>
      <circle cx="92" cy="74" r="17" stroke-width="1.3"/><circle cx="92" cy="74" r="14" stroke-width=".3" stroke-dasharray="1 .6"/>
      <circle cx="153" cy="74" r="17" stroke-width="1.3"/><circle cx="153" cy="74" r="14" stroke-width=".3" stroke-dasharray="1 .6"/>
      <circle cx="214" cy="74" r="17" stroke-width="1.3"/><circle cx="214" cy="74" r="14" stroke-width=".3" stroke-dasharray="1 .6"/>
    </g>
    <g fill="none" stroke="var(--red)" stroke-width=".8">
      <path d="M25 77h12v-3l-2-3h-8l-2 3z"/><circle cx="27.5" cy="78" r=".9"/><circle cx="34.5" cy="78" r=".9"/>
      <rect x="88" y="67" width="7" height="12" rx="1"/><path d="M93 74h4"/>
      <rect x="147" y="70" width="12" height="8"/><path d="M147 70l6 5 6-5"/>
      <circle cx="211" cy="76" r="3"/><circle cx="217" cy="76" r="3"/><circle cx="214" cy="71" r="3"/>
    </g>
    <g stroke="var(--slate)" stroke-width="1.1" fill="none">
      <path d="M55 74h9M61 71l3 3-3 3"/><path d="M116 74h9M122 71l3 3-3 3"/><path d="M177 74h9M183 71l3 3-3 3"/>
    </g>
    <g fill="var(--red)"><rect x="27" y="101" width="8" height=".6"/><rect x="88" y="101" width="8" height=".6"/><rect x="149" y="101" width="8" height=".6"/><rect x="210" y="101" width="8" height=".6"/></g>
  </svg>
  <div class="label" style="left:11px;top:94px;width:40px">Vehicles</div>
  <div class="label" style="left:72px;top:94px;width:40px">Smartphones</div>
  <div class="label" style="left:133px;top:94px;width:40px">Email</div>
  <div class="label" style="left:194px;top:94px;width:40px">Dollar Signs</div>
  <footer class="footer"><span class="copy">© 2024 Plorven Ads. All Rights Reserved.</span><span class="page">Page | 01</span></footer>
</section>

<!-- Slide 2 -->
<section class="slide" style="left:335px;top:51px">
  <div class="rule"></div>
  <div class="brand"><i></i>Plorven Ads</div>
  <h1 class="title">Multiple Lead Sources Feeding into the Program</h1>
  <svg width="245" height="137">
    <path d="M19 42h74l-10 23H29z" fill="var(--red)"/>
    <path d="M30 72h52l-10 23H40z" fill="var(--slate)"/>
    <path d="M41 101h30l-10 22h-10z" fill="var(--red)"/>
    <circle cx="56" cy="53" r="8" fill="#fff"/><circle cx="56" cy="83" r="7" fill="#fff"/><circle cx="56" cy="111" r="6.5" fill="#fff"/>
    <g fill="var(--red)"><circle cx="56" cy="51" r="3"/><rect x="52" y="55" width="8" height="2.5" rx="1"/></g>
    <g fill="var(--red)"><rect x="52" y="80" width="8" height="6"/></g>
    <g fill="var(--slate)"><rect x="52.5" y="108.5" width="7" height="5" rx=".6"/></g>
    <path d="M52.5 109l3.5 2.5 3.5-2.5" stroke="#fff" stroke-width=".6" fill="none"/>
  </svg>
  <div class="small" style="left:95px;top:56px;font-size:4.4px;color:var(--red)">01</div>
  <div class="small" style="left:106px;top:55px;font-size:4.4px;color:var(--ink);font-weight:500">Pre-Qualification Tool</div>
  <div class="small" style="left:106px;top:62px;font-size:3.5px;width:130px">Converts Web Traffic into the highest quality lead on the market</div>
  <div class="small" style="left:95px;top:73px;font-size:4.4px;color:var(--red)">02</div>
  <div class="small" style="left:106px;top:72px;font-size:4.4px;color:var(--ink);font-weight:500">Vorqel Email/Mail Marketing</div>
  <div class="small" style="left:106px;top:79px;font-size:3.5px;width:128px">Delivers actionable leads from email marketing not Just OPENS AND CLICKS. Show the text demo. Audiences below</div>
  <div class="small" style="left:106px;top:91px;font-size:3px;width:130px;line-height:6px">1. Past Sold Customers (Equity Targets)<br>2. Past Service Only Department Customers (Conquest Sales)<br>3. Unsold Leads (from previous interactions)</div>
  <footer class="footer"><span class="copy">© 2024 Plorven Ads. All Rights Reserved.</span><span class="page">Page | 02</span></footer>
</section>

<!-- Slide 3 -->
<section class="slide" style="left:620px;top:51px">
  <div class="rule"></div>
  <div class="brand"><i></i>Plorven Ads</div>
  <h1 class="title">Pre-Qualified Leads: Offering Trade-In Appraisal</h1>
  <div class="photo" style="left:13px;top:44px;width:69px;height:72px;background:var(--red)"></div>
  <div class="photo" role="img" aria-label="Hand holding a phone with a trade-in app over a car engine bay" style="left:10px;top:41px;width:69px;height:72px;background:linear-gradient(135deg,#4a4a4e,#1f1f22 60%,#6b4a2a)"></div>
  <div class="bubble" style="left:55px;top:36px;width:35px;height:20px">Pre-Qualified<br>Flow</div>
  <svg width="245" height="137">
    <circle cx="110" cy="68" r="17" fill="var(--soft)"/><circle cx="164" cy="68" r="17" fill="var(--soft)"/><circle cx="217" cy="68" r="17" fill="var(--soft)"/>
    <g fill="var(--red)"><circle cx="110" cy="63" r="3"/><circle cx="104" cy="65" r="2.3"/><circle cx="116" cy="65" r="2.3"/><path d="M104 75a6 6 0 0 1 12 0z"/><path d="M100 75a4 4 0 0 1 6-3v3z"/><path d="M120 75a4 4 0 0 0-6-3v3z"/></g>
    <path d="M156 72a8 8 0 0 1 16 0" stroke="var(--slate)" stroke-width="3" fill="none" stroke-dasharray="3 1"/><path d="M164 72l3-5" stroke="var(--slate)" stroke-width="1.2"/>
    <path d="M209 70l16-8-5 14-3-4z" fill="var(--red)"/>
    <g fill="var(--red)"><circle cx="133" cy="68" r=".9"/><circle cx="136" cy="68" r=".9"/><circle cx="139" cy="68" r=".9"/><circle cx="187" cy="68" r=".9"/><circle cx="190" cy="68" r=".9"/><circle cx="193" cy="68" r=".9"/></g>
  </svg>
  <div class="label" style="left:88px;top:90px;width:44px">Customer pre-qualifies via Fast4Loan</div>
  <div class="label" style="left:142px;top:90px;width:44px">Receives credit approval</div>
  <div class="label" style="left:195px;top:90px;width:44px">Email and Mail</div>
  <footer class="footer"><span class="copy">© 2024 Plorven Ads. All Rights Reserved.</span><span class="page">Page | 03</span></footer>
</section>

<!-- Slide 4 -->
<section class="slide" style="left:904px;top:51px">
  <div class="rule"></div>
  <div class="brand"><i></i>Plorven Ads</div>
  <h1 class="title">Trade-In Leads: Offering Credit Pre-Qualification</h1>
  <div class="photo" style="left:13px;top:49px;width:69px;height:71px;background:var(--red)"></div>
  <div class="photo" role="img" aria-label="Hand holding a phone showing a trade-in value over a car engine bay" style="left:10px;top:46px;width:69px;height:71px;background:linear-gradient(135deg,#4a4a4e,#1f1f22 60%,#6b4a2a)"></div>
  <div class="bubble" style="left:55px;top:40px;width:35px;height:20px">pre-qualify<br>for a loan.</div>
  <svg width="245" height="137">
    <circle cx="111" cy="73" r="17" fill="var(--soft)"/><circle cx="164" cy="73" r="17" fill="var(--soft)"/><circle cx="218" cy="73" r="17" fill="var(--soft)"/>
    <path d="M106 70a6 6 0 0 0 10 0l-2-5h-6z" fill="var(--slate)"/><circle cx="113" cy="77" r="3.5" fill="var(--slate)"/><path d="M111 77l1.5 1.5 3-3" stroke="#fff" stroke-width=".7" fill="none"/>
    <g fill="var(--red)"><rect x="157" y="73" width="2" height="6"/><rect x="160" y="70" width="2" height="9"/><rect x="163" y="74" width="2" height="5"/><rect x="166" y="71" width="2" height="8"/><rect x="169" y="72" width="2" height="7"/></g>
    <path d="M157 69l4-3 4 2 5-4" stroke="var(--red)" stroke-width=".8" fill="none"/>
    <circle cx="218" cy="73" r="7" fill="none" stroke="var(--slate)" stroke-width="2"/><text x="218" y="75.5" font-size="7" text-anchor="middle" fill="var(--slate)" font-family="Montserrat, sans-serif" font-weight="600">$</text>
    <g fill="var(--red)"><circle cx="134" cy="73" r=".9"/><circle cx="137" cy="73" r=".9"/><circle cx="140" cy="73" r=".9"/><circle cx="188" cy="73" r=".9"/><circle cx="191" cy="73" r=".9"/><circle cx="194" cy="73" r=".9"/></g>
  </svg>
  <div class="label" style="left:89px;top:94px;width:44px">Customer texts for vehicle value</div>
  <div class="label" style="left:142px;top:94px;width:44px">Receives trade-in appraisal</div>
  <div class="label" style="left:194px;top:94px;width:48px">Offer to pre-qualify for financing</div>
  <footer class="footer"><span class="copy">© 2024 Plorven Ads. All Rights Reserved.</span><span class="page">Page | 04</span></footer>
</section>

<!-- Slide 5 -->
<section class="slide" style="left:51px;top:221px">
  <div class="rule"></div>
  <div class="brand"><i></i>Plorven Ads</div>
  <h1 class="title" style="top:11px">Cross-Offer Opportunities</h1>
  <div class="small" style="left:13px;top:34px;width:70px;font-size:3.8px;color:var(--ink);font-weight:500;line-height:6px">Cross-Offer Opportunities for Maximum Engagement</div>
  <div class="small" style="left:91px;top:34px;width:70px;font-size:3.8px;color:var(--ink);font-weight:500;line-height:6px">Engage to Convert one lead type to get both with Email / Mail and Digital Retargeting</div>
  <div class="small" style="left:169px;top:34px;width:72px;font-size:3.8px;color:var(--ink);font-weight:500;line-height:6px">Leverage Email &amp; Social Retarget to Drive Cross-Action</div>
  <svg width="245" height="137">
    <line x1="162" y1="50" x2="162" y2="122" stroke="#ccc" stroke-width=".4"/>
    <g fill="var(--slate)"><circle cx="20" cy="65" r="5"/><circle cx="43" cy="65" r="5"/><circle cx="67" cy="65" r="5"/>
      <circle cx="182" cy="75" r="5"/><circle cx="205" cy="75" r="5"/><circle cx="229" cy="75" r="5"/></g>
    <g stroke="var(--red)" stroke-width=".6" fill="none"><path d="M28 64h7M28 66.5h7"/><path d="M51 64h7M51 66.5h7"/><path d="M190 74h7M190 76.5h7"/><path d="M213 74h7M213 76.5h7"/></g>
    <g fill="#fff"><circle cx="20" cy="65" r="2"/><circle cx="43" cy="65" r="2"/><circle cx="67" cy="65" r="2"/><circle cx="182" cy="75" r="2"/><circle cx="205" cy="75" r="2"/><circle cx="229" cy="75" r="2"/></g>
    <g fill="none" stroke="var(--slate)" stroke-width=".4"><circle cx="120" cy="62" r="3.5"/><circle cx="95" cy="86" r="3.5"/><circle cx="146" cy="86" r="3.5"/>
      <circle cx="191" cy="58" r="3.5"/><circle cx="206" cy="58" r="3.5"/><circle cx="221" cy="58" r="3.5"/></g>
    <g stroke="var(--slate)" stroke-width=".5"><path d="M120 75v-8"/><path d="M110 86h-9"/><path d="M130 86h10"/></g>
  </svg>
  <div class="photo" role="img" aria-label="Businessman in a light shirt standing at the centre of the channels" style="left:110px;top:75px;width:20px;height:22px;border-radius:50%;background:linear-gradient(160deg,#c9b8a5,#8fa3b8)"></div>
  <div class="small" style="left:6px;top:72px;width:30px;font-size:2.2px;text-align:center">Credit Lead</div>
  <div class="small" style="left:29px;top:72px;width:30px;font-size:2.2px;text-align:center">Offer Trade-In</div>
  <div class="small" style="left:52px;top:72px;width:30px;font-size:2.2px;text-align:center;line-height:2.8px">Offer Credit Pre-Qualification</div>
  <div class="small" style="left:168px;top:82px;width:30px;font-size:2.2px;text-align:center">Credit Lead</div>
  <div class="small" style="left:191px;top:82px;width:30px;font-size:2.2px;text-align:center">Offer Trade-In</div>
  <div class="small" style="left:214px;top:82px;width:30px;font-size:2.2px;text-align:center;line-height:2.8px">Offer Credit Pre-Qualification</div>
  <div class="small" style="left:91px;top:105px;width:66px;font-size:2.4px;line-height:3.3px">Whether a lead starts as a Pre-Qualified Credit Lead or a Trade-In Valuation Lead, we use personalized Email/Mail Campaigns and Digital Retargeting Ads (Chatterbook &amp; Snapgrove) to encourage them to take the next action.</div>
  <div class="small" style="left:169px;top:105px;width:60px;font-size:2.4px;line-height:3.3px">Stay Top of Mind and Convert Leads into Multi-Action Customers</div>
  <footer class="footer"><span class="copy">© 2024 Plorven Ads. All Rights Reserved.</span><span class="page">Page | 05</span></footer>
</section>

<!-- Slide 6 -->
<section class="slide" style="left:335px;top:221px">
  <div class="rule"></div>
  <div class="brand"><i></i>Plorven Ads</div>
  <h1 class="title">Continuous Engagement Throughout the Lead Life Cycle</h1>
  <svg width="245" height="137">
    <defs><clipPath id="ring"><circle cx="58" cy="81" r="36"/></clipPath></defs>
    <g clip-path="url(#ring)">
      <rect x="20" y="44" width="76" height="76" fill="var(--slate)"/>
      <rect x="20" y="68" width="76" height="23" fill="var(--red)"/>
      <rect x="57.2" y="44" width="1.2" height="24" fill="#fff"/>
      <rect x="20" y="67" width="76" height="1.2" fill="#fff"/>
      <rect x="20" y="91" width="76" height="1.2" fill="#fff"/>
    </g>
    <g fill="var(--red)"><circle cx="50" cy="68" r="1.2"/><circle cx="66" cy="68" r="1.2"/><circle cx="35" cy="79" r="1.2"/><circle cx="81" cy="79" r="1.2"/><circle cx="58" cy="91.5" r="1.2"/></g>
    <g fill="none" stroke="#fff" stroke-width=".6"><circle cx="48" cy="53" r="3.5"/><circle cx="68" cy="53" r="3.5"/><circle cx="48" cy="79" r="3.5"/><circle cx="51" cy="104" r="3.5"/></g>
  </svg>
  <div class="small" style="left:39px;top:62px;font-size:3.2px;color:#fff">Lorem Ips</div>
  <div class="small" style="left:61px;top:62px;font-size:3.2px;color:#fff">Lorem Ips</div>
  <div class="small" style="left:56px;top:76px;font-size:3.2px;color:#fff;line-height:4.2px">Sed ut<br>perspiciatis</div>
  <div class="small" style="left:57px;top:102px;font-size:3.2px;color:#fff">Lorem ipsum</div>
  <div class="small" style="left:111px;top:57px;width:121px;font-size:3.4px;line-height:5.9px">Sed ut perspiciatis unde omnis iste natus error sit voluptatem accusantium doloremque laudantium, totam rem aperiam, eaque ipsa quae ab illo inventore veritatis et quasi architecto beatae vitae dicta sunt explicabo. Nemo enim ipsam voluptatem quia voluptas sit aspernatur aut odit aut fugit, sed quia consequuntur magni dolores eos qui ratione voluptatem sequi nesciunt. Neque porro quisquam est, qui dolorem ipsum quia dolor sit amet, consectetur, adipisci velit,</div>
  <footer class="footer"><span class="copy">© 2024 Plorven Ads. All Rights Reserved.</span><span class="page">Page | 06</span></footer>
</section>

<!-- Slide 7 -->
<section class="slide" style="left:620px;top:221px">
  <div class="rule"></div>
  <div class="brand"><i></i>Plorven Ads</div>
  <h1 class="title" style="top:11px">Converting Leads into Sales</h1>
  <div class="photo" style="left:56px;top:44px;width:65px;height:71px;background:var(--red)"></div>
  <div class="photo" role="img" aria-label="Smiling woman in a car being handed the keys to her new vehicle" style="left:12px;top:40px;width:106px;height:71px;background:linear-gradient(120deg,#cfd6dc,#8d97a0 45%,#e8ddd2)"></div>
  <div class="small" style="left:141px;top:50px;font-size:3.5px;color:var(--ink)">Convert both credit and trade leads into sales</div>
  <svg width="245" height="137">
    <g fill="var(--slate)">
      <rect x="141.5" y="87" width="2.6" height="10.5"/><rect x="153.5" y="76" width="2.6" height="21.5"/><rect x="165.5" y="83" width="2.6" height="14.5"/><rect x="177.5" y="83" width="2.6" height="14.5"/>
      <rect x="189.5" y="63" width="2.6" height="34.5"/><rect x="201.5" y="61" width="2.6" height="36.5"/><rect x="213.5" y="66" width="2.6" height="31.5"/><rect x="225.5" y="64" width="2.6" height="33.5"/>
    </g>
    <g fill="var(--red)">
      <rect x="141.5" y="88" width="2.6" height="9.5"/><rect x="153.5" y="83" width="2.6" height="14.5"/><rect x="165.5" y="83" width="2.6" height="14.5"/><rect x="177.5" y="83" width="2.6" height="14.5"/>
      <rect x="189.5" y="70" width="2.6" height="27.5"/><rect x="201.5" y="75" width="2.6" height="22.5"/><rect x="213.5" y="73" width="2.6" height="24.5"/><rect x="225.5" y="71" width="2.6" height="26.5"/>
    </g>
    <g font-size="3.4" fill="var(--ink)" text-anchor="middle" font-family="Montserrat, sans-serif">
      <text x="142.8" y="103">A</text><text x="154.8" y="103">B</text><text x="166.8" y="103">C</text><text x="178.8" y="103">D</text><text x="190.8" y="103">E</text><text x="202.8" y="103">F</text><text x="214.8" y="103">G</text><text x="226.8" y="103">H</text>
    </g>
  </svg>
  <footer class="footer"><span class="copy">© 2024 Plorven Ads. All Rights Reserved.</span><span class="page">Page | 07</span></footer>
</section>

<!-- Slide 8 -->
<section class="slide" style="left:904px;top:221px">
  <div class="rule"></div>
  <div class="brand"><i></i>Plorven Ads</div>
  <h1 class="title" style="width:175px">Maximize Lead Potential with Cross-Offer Opportunities</h1>
  <div class="photo" style="left:120px;top:49px;width:89px;height:71px;background:var(--red)"></div>
  <div class="photo" role="img" aria-label="Happy man in a new car holding out a fist through the window" style="left:36px;top:43px;width:167px;height:72px;background:linear-gradient(110deg,#e9eef3,#b7c1cb 45%,#6f6a66 70%,#d9dfe4)"></div>
  <footer class="footer"><span class="copy">© 2024 Plorven Ads. All Rights Reserved.</span><span class="page">Page | 08</span></footer>
</section>

</body>
</html>
```